Marwick Law Letterhead

We need a new letterhead design for a Law Firm. The address for the law firm is 1475 Calloway Street, Suite 210, Houston, Texas 77041. Phone Number: 832-361-9027; Fax Number: 832-614-7359. The logo is uploaded to the project.

```html
<!DOCTYPE html>
<html lang="en">
<head>
<meta charset="utf-8">
<title>Marwick Law Letterhead</title>
<link rel="stylesheet" href="https://fonts.googleapis.com/css2?family=Montserrat:wght@400;500;600&display=swap">
<style>
  :root {
    --navy: #1c3164;
    --navy-dark: #14264f;
    --red: #d71f2b;
    --red-dark: #7d0f18;
    --ink: #2b2b2b;
    --paper: #ffffff;
    --backdrop: #e8e8e8;
  }
  * { margin: 0; padding: 0; box-sizing: border-box; }
  html, body {
    width: 1154px; height: 1200px; overflow: hidden;
    background: var(--backdrop);
    font-family: "Montserrat", Arial, sans-serif;
    color: var(--ink);
  }
  .letterhead {
    position: absolute; left: 162px; top: 20px;
    width: 830px; height: 1160px;
    background: var(--paper);
    box-shadow: 0 2px 10px rgba(0,0,0,0.12);
  }
  .brand {
    position: absolute; left: 32px; top: 62px;
    display: flex; align-items: center; gap: 10px;
  }
  .brand-mark {
    width: 44px; height: 44px; border-radius: 50%;
    background: var(--navy);
  }
  .brand-name {
    font-size: 30px; font-weight: 600; color: var(--navy);
    letter-spacing: 0.5px;
  }
  .contact {
    position: absolute; left: 630px; top: 46px;
    font-size: 14px; line-height: 18px; color: #1a1a1a;
  }
  .contact address { font-style: normal; margin-bottom: 8px; }
  .contact-line { display: flex; align-items: center; gap: 10px; line-height: 21px; }
  .contact-line svg { width: 12px; height: 12px; }
  .rule {
    position: absolute; left: 30px; width: 768px;
  }
  .rule-navy { top: 180px; height: 2px; background: var(--navy); }
  .rule-red { top: 184px; height: 3px; background: var(--red); }
  .recipient {
    position: absolute; left: 31px; top: 276px;
    font-size: 13.5px; line-height: 20.6px; color: #1a1a1a;
  }
  .letter-body {
    position: absolute; left: 33px; top: 365px; width: 768px;
    font-size: 13.4px; line-height: 20.6px; text-align: justify;
  }
  .letter-body p { margin-bottom: 20.6px; }
  .closing {
    position: absolute; left: 31px; top: 945px;
    font-size: 16px; color: #1a1a1a;
  }
  .signature {
    position: absolute; left: 30px; top: 976px;
    width: 92px; height: 28px; background: #e9e9e9; border-radius: 3px;
  }
  .footer-band {
    position: absolute; left: 0; top: 1078px; width: 830px; height: 47px;
  }
  .web {
    position: absolute; left: 497px; top: 1092px;
    display: flex; align-items: center; gap: 7px;
    font-size: 14px; color: #fff;
  }
  .web svg { width: 13px; height: 13px; }
</style>
</head>
<body>
<main class="letterhead">
  <header>
    <div class="brand">
      <span class="brand-mark"></span>
      <span class="brand-name">Marwick Law</span>
    </div>
    <div class="contact">
      <address>1475 Calloway Street,<br>Suite 210, Houston,<br>Texas 77041</address>
      <div class="contact-line">
        <svg viewBox="0 0 12 12"><path fill="var(--red)" d="M2.5 1l2 2.2-1 1.3c.7 1.5 1.8 2.6 3.3 3.3l1.3-1 2.2 2-1.2 1.9C5.3 10.5 1.5 6.7 1.3 2.2z"/></svg>
        <span>832-361-9027</span>
      </div>
      <div class="contact-line">
        <svg viewBox="0 0 12 12"><rect x="3" y="1" width="6" height="3" fill="var(--red)"/><rect x="1" y="4.5" width="10" height="5" rx="1" fill="var(--red)"/><rect x="3" y="8" width="6" height="3" fill="#fff" stroke="var(--red)"/></svg>
        <span>832-614-7359</span>
      </div>
    </div>
    <div class="rule rule-navy"></div>
    <div class="rule rule-red"></div>
  </header>

  <section class="recipient">
    <div>Mr/s</div>
    <div>First Name and Last Name</div>
    <div>Company Name</div>
    <div>Address</div>
  </section>

  <section class="letter-body">
    <p>Lorem ipsum dolor sit amet,consectetur adipiscing sed do eiusmod tempor incididunt laboreet dolore magna aliqua.Ut enim ad minim.veniam, quis nostrud exercitation ullamco laboris nisi ut aliquip exea commodo consequat.Lorem ipsum dolor sit amet,consectetur adipiscing sed do eiusmod tempor incididunt.labore et dolore magna aliqua. Ut enim</p>
    <p>Lorem ipsum dolor sit amet, consectetur adipiscing sed do eiusmod tempor incididunt labore et dolore magna aliqua. Ut enim ad minim veniam, quis nostrud exercitation ullamco laboris nisi ut aliquip exea commodo consequat.Duis aute irure dolor in reprehenderit in voluptate velit esse cillum irure dolor in reprehenderit in voluptate velit esse irure</p>
    <p>Lorem ipsum dolor sit amet, consectetur adipiscing sed do eiusmod tempor incididunt labore et dolore magna aliqua. consequat. Duis aute irure dolor in.reprehenderit in voluptate velit esse cillum dolore eu fugiat nulla pariatur. Excepteur sint occaecat cupidatat non proident, sunt in culpa qui officia deserunt mollit,</p>
    <p>Lorem ipsum dolor sit amet, consectetur adipiscing sed do eiusmod tempor incididunt labore et dolore magna aliqua. Ut enim Lorem ipsum dolor sit amet, consectetur adipiscing sed do eiusmod tempor incididunt labore et dolore magna aliqua. Ut enim Lorem ipsum aliqua.ipsum</p>
    <p>Lorem ipsum dolor sit amet, consectetur adipiscing sed do eiusmod tempor incididunt labore et dolore magna aliqua. Ut enim ad minim veniam, quis nostrud exercitation ullamco laboris nisi ut aliquip exea commodo consequat.Duis aute irure dolor in reprehenderit in voluptate velit esse cillum irure dolor in reprehenderit in voluptate velit esse irure</p>
    <p>Lorem ipsum dolor sit amet, consectetur adipiscing sed do eiusmod tempor incididunt labore et dolore magna aliqua. Ut enim ad minim veniam, quis nostrud exercitation ullamco laboris nisi ut aliquip exea commodo consequat.Duis aute irure dolor in reprehenderit in voluptate velit esse cillum irure dolor in reprehenderit in voluptate velit esse irure</p>
  </section>

  <div class="closing">Regards</div>
  <div class="signature" role="img" aria-label="Handwritten signature"></div>

  <footer>
    <svg class="footer-band" viewBox="0 0 830 47" preserveAspectRatio="none">
      <defs>
        <linearGradient id="navyFade" x1="0" x2="1">
          <stop offset="0" stop-color="var(--navy-dark)"/>
          <stop offset="1" stop-color="var(--navy)"/>
        </linearGradient>
        <linearGradient id="redFade" x1="0" x2="1">
          <stop offset="0.3" stop-color="var(--red)"/>
          <stop offset="1" stop-color="var(--red-dark)"/>
        </linearGradient>
      </defs>
      <polygon points="0,0 489,0 457,47 0,47" fill="url(#navyFade)"/>
      <polygon points="500,0 694,0 662,47 468,47" fill="url(#redFade)"/>
      <polygon points="705,0 830,0 830,47 673,47" fill="var(--navy)"/>
    </svg>
    <div class="web">
      <svg viewBox="0 0 12 12"><circle cx="6" cy="6" r="5.5" fill="#fff"/><path d="M3 4c1 0 2 1 1.5 2S5 8 6 8.5M8 2.5c-.5 1 .5 1.5 1.5 1.5M7.5 10c0-1 1-1.5 2-1.5" stroke="var(--red)" stroke-width="1.2" fill="none"/></svg>
      <span>www.marwicklaw.com</span>
    </div>
  </footer>
</main>
</body>
</html>
```